Lorna Vale Industries Wix Site

Company website run as a hobby by my daughter Lorna. She wants to be able to offer multiple products for sale online (so etail enabled). Personalized products like bracelets and necklaces with people's names. Piggy Banks with kids names. Trail Keeper cookies when in season. Not childish in presentation but easy to navigate by kids. Big images like on original website (lornavalebakes.com). Same humor as on that site (go to the cart and empty it and you will get the idea. Colors Gold like on the bird in her attached card. Blue should be lighter than that card (robins egg type of blue). Avoid the green on the biz card. Basics of a new website with About Us, Contact, social media and a cart with payment options via coinrill. mobile version nice to have but not mandataory.

```html
<!DOCTYPE html>
<html lang="en">
<head>
<meta charset="utf-8">
<title>Lorna Vale Industries</title>
<link rel="stylesheet" href="https://fonts.googleapis.com/css2?family=Open+Sans:ital,wght@0,400;0,600;1,700&family=Exo+2:wght@600;700&family=Oswald:wght@400&display=swap">
<style>
  :root {
    --gold: #b39128;
    --gold-dark: #a3831f;
    --orange: #e39c00;
    --orange-deep: #d58b00;
    --teal: #1ea7b8;
    --sky: #72e5ef;
    --grey-box: #cfcfcf;
    --grey-band: #f0f0f0;
    --ink: #2a2a2a;
    --text: #555;
    --white: #fff;
  }
  * { box-sizing: border-box; margin: 0; padding: 0; }
  html, body { width: 791px; height: 1200px; overflow: hidden; background: var(--white); }
  body { position: relative; font-family: "Open Sans", sans-serif; color: var(--ink); }
  .abs { position: absolute; }

  /* Header */
  .brand { left: 62px; top: 14px; width: 100px; text-align: center; }
  .brand-mark { width: 34px; height: 34px; border-radius: 50%; background: var(--gold); margin: 6px auto 8px; }
  .brand-name { font-size: 16px; font-weight: 400; color: #333; }
  .search { left: 455px; top: 21px; width: 158px; height: 22px; border: 1px solid #bbb; }
  .search-btn { position: absolute; right: -1px; top: -1px; width: 23px; height: 22px; background: var(--teal); }
  .cart-label { left: 629px; top: 26px; font-size: 9.5px; color: #444; }
  .cart-icon { left: 695px; top: 16px; }
  .nav { left: 355px; top: 60px; height: 47px; display: flex; font-size: 9.5px; font-weight: 600; color: #333; }
  .nav a { color: inherit; text-decoration: none; display: flex; align-items: center; padding: 0 15px; }
  .nav a.active { background: #eeeeee; border-top: 2px solid var(--gold); }

  /* Hero */
  .hero { left: 0; top: 107px; width: 791px; height: 427px; background: linear-gradient(90deg, var(--orange) 0%, var(--orange) 55%, var(--orange-deep) 100%); }
  .hero-photo { position: absolute; left: 395px; top: 40px; width: 350px; height: 387px; border-radius: 48% 48% 12% 12%; background: radial-gradient(ellipse at 45% 40%, #ffffff 0%, #eeeeea 60%, #d9d4c4 100%); }
  .hero-title { left: 67px; top: 162px; font-size: 24px; font-weight: 700; font-style: italic; color: #262626; }
  .hero-text { left: 67px; top: 206px; width: 320px; font-size: 12.5px; line-height: 17px; color: #2a2a2a; }
  .btn { top: 257px; width: 99px; height: 26px; font-size: 11px; font-weight: 600; display: flex; align-items: center; justify-content: center; }
  .btn-fill { left: 67px; background: var(--teal); color: var(--white); }
  .btn-line { left: 180px; border: 1px solid #3a2a00; color: #2a2a2a; }
  .dots { left: 374px; top: 407px; display: flex; gap: 8px; }
  .dots span { width: 9px; height: 9px; border-radius: 50%; border: 1.5px solid var(--white); }
  .dots span.on { background: var(--white); }

  /* Feature boxes */
  .promo { top: 567px; width: 214px; height: 156px; color: var(--white); font-family: "Exo 2", sans-serif; font-weight: 700; text-align: center; }
  .promo-new { left: 66px; background: var(--gold); box-shadow: 0 3px 4px rgba(0,0,0,.25); }
  .promo-new .line { font-size: 17px; line-height: 28px; padding-top: 24px; }
  .promo-new .year { font-size: 52px; line-height: 54px; }
  .promo-call { left: 289px; background: var(--grey-box); font-weight: 600; }
  .promo-call .line { font-size: 19px; line-height: 27px; padding-top: 24px; }
  .promo-call .phone { display: flex; align-items: center; justify-content: center; gap: 8px; font-size: 20px; margin-top: 8px; }
  .promo-fan { left: 512px; background: var(--sky); }
  .promo-fan .line { font-size: 17px; line-height: 22px; padding-top: 26px; }
  .promo-fan .sub { font-size: 13px; line-height: 20px; margin-top: 14px; }

  /* New products */
  .band { left: 0; top: 761px; width: 791px; height: 31px; background: var(--grey-band); }
  .band-tab { left: 66px; top: 761px; width: 101px; height: 31px; background: var(--gold); color: var(--white); font-family: "Oswald", sans-serif; font-size: 14px; display: flex; align-items: center; justify-content: center; letter-spacing: -.3px; }
  .arrow { top: 761px; width: 22px; height: 31px; display: flex; align-items: center; justify-content: center; }
  .arrow-prev { left: 681px; background: #c8c8c8; }
  .arrow-next { left: 703px; background: var(--gold); }
  .product { top: 819px; width: 155px; height: 236px; border: 1px solid #d6d6d6; overflow: hidden; }
  .product-img { position: absolute; left: 12px; right: 12px; top: 40px; height: 140px; border-radius: 8px; }
  .img-bangles { background: radial-gradient(ellipse, #e0b24a 0%, #d6a437 45%, #f5efe0 75%, #fff 100%); top: 55px; height: 110px; }
  .img-heart { background: radial-gradient(ellipse, #9a9a9a 0%, #cfcfcf 50%, #fff 80%); }
  .img-necklace { background: radial-gradient(ellipse at 50% 65%, #2fb1b0 0%, #7fcac6 40%, #f0e8d8 70%, #fff 90%); top: 20px; height: 170px; }
  .img-piggy { background: radial-gradient(ellipse, #ef8fb0 0%, #f4b3c9 50%, #fff 80%); top: 40px; }
  .ribbon { position: absolute; right: -28px; top: 14px; width: 110px; height: 22px; background: var(--teal); color: var(--white); font-size: 9.5px; transform: rotate(45deg); display: flex; align-items: center; justify-content: center; }
  .actions { position: absolute; left: 0; bottom: 0; width: 155px; height: 44px; display: flex; gap: 1px; }
  .actions span { flex: 1; display: flex; align-items: center; justify-content: center; background: #999; }
  .actions span.buy { background: var(--gold); }
  .caption { top: 1062px; width: 155px; text-align: center; font-size: 11px; color: #555; letter-spacing: .3px; }

  /* Footer */
  .footer { left: 0; top: 1134px; width: 791px; height: 66px; background: var(--gold); color: var(--white); }
  .footer-nav { position: absolute; left: 0; width: 791px; top: 10px; display: flex; justify-content: center; font-size: 9.5px; font-weight: 600; }
  .footer-nav span.sep { margin: 0 18px; }
  .footer-rule { position: absolute; left: 0; top: 33px; width: 791px; border-top: 1px solid #c7a94a; }
  .copyright { position: absolute; left: 67px; top: 44px; font-size: 8.5px; }
  .social { position: absolute; left: 670px; top: 43px; display: flex; gap: 7px; }
  .social span { width: 14px; height: 14px; border-radius: 50%; background: var(--white); }
</style>
</head>
<body>

<header>
  <div class="abs brand">
    <div class="brand-mark"></div>
    <div class="brand-name">LornaBiz</div>
  </div>
  <div class="abs search">
    <div class="search-btn">
      <svg width="23" height="22" viewBox="0 0 23 22"><circle cx="10.5" cy="10" r="4" fill="none" stroke="#fff" stroke-width="1.6"/><line x1="13.5" y1="13" x2="16" y2="15.5" stroke="#fff" stroke-width="1.8"/></svg>
    </div>
  </div>
  <div class="abs cart-label">Cart (empty)</div>
  <svg class="abs cart-icon" width="32" height="26" viewBox="0 0 32 26">
    <path d="M1 3h5l4 13h16l4-10H8" fill="none" stroke="#1ea7b8" stroke-width="2.6" stroke-linejoin="round"/>
    <line x1="11" y1="10" x2="28" y2="10" stroke="#1ea7b8" stroke-width="2"/>
    <circle cx="12" cy="22" r="2.2" fill="#1ea7b8"/><circle cx="23" cy="22" r="2.2" fill="#1ea7b8"/>
  </svg>
  <nav class="abs nav">
    <a class="active">Home</a><a>About Us</a><a>Shop</a><a>Gallery</a><a>Orders</a><a>Contact Us</a>
  </nav>
</header>

<section class="abs hero">
  <div class="hero-photo" role="img" aria-label="Photo of a white personalised piggy bank with a child's name"></div>
  <h1 class="abs hero-title">Lorna Vale Industries</h1>
  <p class="abs hero-text">We Personalised products like bracelets and necklaces with people's names. Piggy Banks with kids names</p>
  <div class="abs btn btn-fill">Read More</div>
  <div class="abs btn btn-line">View Works</div>
  <div class="abs dots"><span class="on"></span><span></span><span></span></div>
</section>

<section>
  <div class="abs promo promo-new">
    <div class="line">CHECK WHAT IS NEW<br>IN</div>
    <div class="year">2014</div>
  </div>
  <div class="abs promo promo-call">
    <div class="line">CALL US<br>ORDER NOW</div>
    <div class="phone">
      <svg width="22" height="38" viewBox="0 0 22 38"><path d="M6 1c-5 3-6 12-2 22s9 14 13 14l3-2-4-8-4 1c-2-3-4-8-4-12l3-2-1-9z" fill="#fff"/></svg>
      <span>1-425-555-0147</span>
    </div>
  </div>
  <div class="abs promo promo-fan">
    <div class="line">BECOME A FAN ON<br>FRIENDLOOP</div>
    <div class="sub">GET ACCESS TO AN EXCLUSIVE<br>OFFERS</div>
  </div>
</section>

<section>
  <div class="abs band"></div>
  <div class="abs band-tab">New Product</div>
  <div class="abs arrow arrow-prev"><svg width="8" height="9"><path d="M7 0v9L0 4.5z" fill="#fff"/></svg></div>
  <div class="abs arrow arrow-next"><svg width="8" height="9"><path d="M1 0v9l7-4.5z" fill="#fff"/></svg></div>

  <div class="abs product" style="left:66px">
    <div class="product-img img-bangles" role="img" aria-label="Photo of two gold bangles"></div>
    <div class="ribbon">$ 292.39</div>
    <div class="actions">
      <span class="buy"><svg width="14" height="18" viewBox="0 0 14 18"><path d="M1 5h12v12H1z" fill="#fff"/><path d="M4 6V3a3 3 0 0 1 6 0v3" fill="none" stroke="#fff" stroke-width="1.4"/></svg></span>
      <span><svg width="14" height="16" viewBox="0 0 14 16"><rect x="4" y="1" width="5" height="8" rx="2.5" fill="none" stroke="#fff" stroke-width="1.6" transform="rotate(25 7 5)"/><rect x="4" y="7" width="5" height="8" rx="2.5" fill="none" stroke="#fff" stroke-width="1.6" transform="rotate(25 7 11)"/></svg></span>
      <span><svg width="18" height="18" viewBox="0 0 18 18"><path d="M3 8a6 6 0 0 1 11-3M15 10a6 6 0 0 1-11 3" fill="none" stroke="#fff" stroke-width="2"/><path d="M15 1v5h-5zM3 17v-5h5z" fill="#fff"/></svg></span>
    </div>
  </div>
  <div class="abs product" style="left:234px">
    <div class="product-img img-heart" role="img" aria-label="Photo of a silver infinity heart pendant"></div>
  </div>
  <div class="abs product" style="left:403px">
    <div class="product-img img-necklace" role="img" aria-label="Photo of a turquoise flower statement necklace"></div>
  </div>
  <div class="abs product" style="left:570px">
    <div class="product-img img-piggy" role="img" aria-label="Photo of a pink piggy bank"></div>
  </div>

  <div class="abs caption" style="left:66px">Lorem ipsum</div>
  <div class="abs caption" style="left:234px">Lorem ipsum</div>
  <div class="abs caption" style="left:403px">Lorem ipsum</div>
  <div class="abs caption" style="left:570px">Lorem ipsum</div>
</section>

<footer class="abs footer">
  <div class="footer-nav">
    <span>Home</span><span class="sep">|</span><span>About Us</span><span class="sep">|</span><span>Shop</span><span class="sep">|</span><span>Gallery</span><span class="sep">|</span><span>Orders</span><span class="sep">|</span><span>Contact Us</span>
  </div>
  <div class="footer-rule"></div>
  <div class="copyright">Yoursite © 2014 All Rights Reserved.</div>
  <div class="social"><span></span><span></span><span></span></div>
</footer>

</body>
</html>
```